Make it cool to work near where you are...

Calling all creatives - create the ultimate cool card for people who want to cut their commute.

Here at PineNook we've got what can best be described as an Flintpass card for desks - and we want to brighten up the wallets of our most loyal users.

So, pitch us your ideas and you might see your design on cards being flashed across the country - and we've thrown in a bit of cash too.

Do see our brief card guidelines - with a couple of past examples thrown in.

```html
<!DOCTYPE html>
<html lang="en">
<head>
<meta charset="utf-8">
<title>PineNook – Business Card</title>
<link rel="stylesheet" href="https://fonts.googleapis.com/css2?family=Lato:wght@400;700;900&display=swap">
<style>
  :root {
    --backdrop: #d6e1e8;
    --charcoal: #3b3b3c;
    --charcoal-deep: #333334;
    --paper: #ffffff;
    --paper-shade: #f1f1f1;
    --magenta: #e8247c;
    --ink-light: #e8e8e8;
  }
  * { margin: 0; padding: 0; box-sizing: border-box; }
  html, body {
    width: 1200px;
    height: 960px;
    overflow: hidden;
  }
  body {
    background: var(--backdrop);
    font-family: "Lato", sans-serif;
    position: relative;
  }
  .card {
    position: absolute;
    left: 286px;
    width: 628px;
    height: 358px;
    border-radius: 20px;
    overflow: hidden;
  }
  .card-front {
    top: 95px;
    background: radial-gradient(ellipse at 50% 45%, #444445 0%, var(--charcoal-deep) 75%);
  }
  .card-back {
    top: 507px;
    background: linear-gradient(180deg, var(--paper) 0%, var(--paper-shade) 45%);
  }
  .wordmark {
    position: absolute;
    left: 0;
    right: 0;
    text-align: center;
    font-weight: 900;
    color: var(--magenta);
    letter-spacing: -2px;
    line-height: 1;
  }
  .card-front .wordmark {
    top: 140px;
    font-size: 84px;
  }
  .card-back .wordmark {
    top: 82px;
    font-size: 46px;
    letter-spacing: -1px;
  }
  .back-swoosh {
    position: absolute;
    left: 0;
    top: 0;
    width: 628px;
    height: 358px;
  }
  .address {
    position: absolute;
    left: 46px;
    top: 221px;
    font-size: 14px;
    line-height: 18px;
    color: var(--ink-light);
  }
  .contact-list {
    position: absolute;
    left: 46px;
    top: 272px;
    list-style: none;
    font-size: 14px;
    color: var(--ink-light);
  }
  .contact-list li {
    display: flex;
    align-items: center;
    height: 20.5px;
  }
  .contact-list svg {
    width: 16px;
    height: 14px;
    margin-right: 9px;
    flex: none;
  }
  .person {
    position: absolute;
    right: 48px;
    top: 260px;
    text-align: right;
    color: var(--ink-light);
  }
  .person-name {
    font-size: 17px;
    font-weight: 700;
    line-height: 22px;
  }
  .person-role {
    font-size: 14px;
    line-height: 18px;
  }
</style>
</head>
<body>

<section class="card card-front">
  <div class="wordmark">PineNook</div>
</section>

<section class="card card-back">
  <div class="wordmark">PineNook</div>

  <svg class="back-swoosh" viewBox="0 0 628 358" aria-hidden="true">
    <path d="M0,160 Q300,222 628,184 L628,358 L0,358 Z" fill="var(--charcoal)"/>
    <path d="M0,146 Q300,200 628,154 L628,181 Q300,214 0,155 Z" fill="var(--magenta)"/>
  </svg>

  <p class="address">NookHouse, 48-52 Harlow Lane<br>N4 2QT London, United Kingdom</p>

  <ul class="contact-list">
    <li>
      <svg viewBox="0 0 16 14" aria-hidden="true"><path d="M1,5 Q8,-1 15,5 L13,7 L11,5 L11,4 Q8,3 5,4 L5,5 L3,7 Z M4,7 L12,7 L14,13 L2,13 Z" fill="var(--ink-light)"/><circle cx="8" cy="10" r="1.6" fill="var(--charcoal)"/></svg>
      +44 20 7946 0123
    </li>
    <li>
      <svg viewBox="0 0 16 14" aria-hidden="true"><rect x="1" y="1.5" width="14" height="11" fill="none" stroke="var(--ink-light)" stroke-width="1.4"/><path d="M1,1.5 L8,8 L15,1.5 M1,12.5 L6,6.5 M15,12.5 L10,6.5" fill="none" stroke="var(--ink-light)" stroke-width="1.2"/></svg>
      team@pinenook.com
    </li>
    <li>
      <svg viewBox="0 0 16 16" aria-hidden="true"><circle cx="8" cy="8" r="6.8" fill="none" stroke="var(--ink-light)" stroke-width="1.3"/><ellipse cx="8" cy="8" rx="3" ry="6.8" fill="none" stroke="var(--ink-light)" stroke-width="1.1"/><path d="M1.2,8 H14.8 M2.5,4.5 H13.5 M2.5,11.5 H13.5" stroke="var(--ink-light)" stroke-width="1.1"/></svg>
      www.pinenook.com
    </li>
  </ul>

  <div class="person">
    <div class="person-name">Sam Carter</div>
    <div class="person-role">Managing Director</div>
  </div>
</section>

</body>
</html>
```